Company or website name
- dalewintham.com
- Links to the website
- Vita Forge
- Describe your company and organization and target audience
- Founded by celebrity personal trainer and media personality Dale Wintham, Vita Forge provides high quality on-site fitness and wellness classes, and personal trainers for businesses and residential gyms throughout New York City. Our target audience are residents of high end buildings in NYC, that expect excellence and luxury
- The design should have the following
- This is a 24"x36" Poster for a complimentary event at a high end building. I would like the poster to look high end, luxury and simple and chique. The words should be clear and easy to read. It would be great to have a final copy that we can send to the printer and one which we can edit for future events Here is the text: The Halcott Spires Gym Complimentary Fitness & Wellness Event Complimentary Yoga, Pilates & Interval Training Bootcamp Classes PLUS: 30 Minute Private Training Sessions *Kids Karate Classes Also Available Saturday May 18th, 25th & June 1st Time: 9:00am - 12:15pm Halcott Spires Gym Schedule: 9:00am - 9:30am Yoga 9:45am - 10:15am Interval Training Bootcamp 11:45am -12:15pm Pilates 9:00am - 12:00pm Private Training Sessions Special Introductory Rate on Future Packages During Promotion www.Vitaforge.tv Info@vitaforge.tv
- Other Facts

```html
<!DOCTYPE html>
<html lang="en">
<head>
<meta charset="utf-8">
<title>Halcott Spires Complimentary Fitness &amp; Wellness Event – Vita Forge</title>
<link href="https://fonts.googleapis.com/css2?family=League+Gothic&family=Oswald:wght@500;600&family=Fira+Sans+Condensed:wght@400;600;700&family=Open+Sans:wght@400;600;700&display=swap" rel="stylesheet">
<style>
  :root {
    --ink: #000000;
    --white: #ffffff;
    --ghost: #5a5a5a;
    --gold: #f7c51e;
    --green-dark: #178a35;
    --green-light: #34ad4c;
    --blue-dark: #0d3fbf;
    --blue-light: #1a63e0;
    --red: #e3262b;
    --muted: #d8d8d8;
  }
  * { box-sizing: border-box; margin: 0; padding: 0; }
  html, body { width: 800px; height: 1200px; overflow: hidden; background: var(--ink); }
  .poster {
    position: relative; width: 800px; height: 1200px; overflow: hidden;
    background: var(--ink); color: var(--white);
    font-family: "Fira Sans Condensed", sans-serif;
  }
  .brand-watermark {
    position: absolute; left: 6px; top: 1200px;
    transform: rotate(-90deg); transform-origin: 0 0;
    width: 1200px; height: 120px;
    font-family: "Oswald", sans-serif; font-weight: 600;
    font-size: 128px; line-height: 120px; letter-spacing: 34px;
    color: var(--ghost); white-space: nowrap; padding-left: 20px;
  }
  .hero-photo { position: absolute; left: 30px; top: 0; width: 300px; height: 1200px; }
  .brand-mark { position: absolute; right: 52px; top: 150px; text-align: center; }
  .brand-mark .dot { width: 22px; height: 22px; border-radius: 50%; background: var(--white); margin: 0 auto 12px; }
  .brand-mark .name { font-family: "Open Sans", sans-serif; font-weight: 700; font-size: 19px; letter-spacing: 0.5px; }
  .brand-mark .founder { font-family: "Open Sans", sans-serif; font-weight: 400; font-size: 14px; color: var(--muted); margin-top: 2px; }
  .rule-top { position: absolute; left: 310px; right: 0; top: 291px; height: 3px; background: var(--white); }
  .event-band {
    position: absolute; left: 295px; right: 0; top: 300px; height: 253px;
    background: linear-gradient(90deg, var(--green-dark), var(--green-light));
    font-family: "League Gothic", "Oswald", sans-serif; font-weight: 400; text-transform: uppercase;
  }
  .event-band div { position: absolute; left: 0; right: 0; text-align: center; white-space: nowrap; }
  .event-band .venue { top: 18px; font-size: 88px; line-height: 88px; letter-spacing: 1px; }
  .event-band .headline { top: 88px; font-size: 92px; line-height: 92px; color: var(--gold); letter-spacing: 5px; }
  .event-band .subline { top: 180px; font-size: 62px; line-height: 62px; letter-spacing: 0.5px; }
  .classes-band {
    position: absolute; left: 328px; right: 0; top: 553px; height: 154px;
    background: linear-gradient(90deg, var(--blue-dark), var(--blue-light));
    text-align: center; padding-top: 10px;
    font-weight: 700; text-transform: uppercase; white-space: nowrap;
  }
  .classes-band .line { font-size: 34px; line-height: 42px; letter-spacing: 1px; }
  .classes-band .wide { letter-spacing: 7px; font-size: 36px; }
  .offer { position: absolute; left: 282px; top: 730px; color: var(--gold); font-weight: 700; text-transform: uppercase; white-space: nowrap; }
  .offer .plus { position: absolute; left: 0; top: -12px; color: var(--red); font-size: 88px; line-height: 80px; font-weight: 600; }
  .offer .big { margin-left: 52px; font-size: 46px; line-height: 48px; letter-spacing: 1px; }
  .offer .small { margin-left: 52px; font-size: 33px; line-height: 34px; letter-spacing: 0.5px; }
  .dates { position: absolute; left: 203px; top: 834px; color: var(--gold); font-weight: 700; font-size: 24px; letter-spacing: 0.3px; text-transform: uppercase; white-space: nowrap; }
  .dates sup { font-size: 12px; }
  .schedule { position: absolute; right: 36px; top: 876px; text-align: right; font-family: "Open Sans", sans-serif; font-size: 23px; line-height: 29px; white-space: nowrap; }
  .schedule h2 { font-size: 23px; font-weight: 700; letter-spacing: 1px; border-bottom: 2px solid var(--white); width: 256px; margin-left: auto; margin-bottom: 8px; }
  .schedule li { list-style: none; margin-bottom: 11px; }
  .schedule li::before { content: "• "; }
  .schedule b { font-weight: 700; }
  .schedule .note { display: block; }
  .rule-bottom { position: absolute; left: 190px; right: 0; top: 1150px; height: 2px; background: linear-gradient(90deg, transparent, var(--white) 20%, var(--white) 80%, transparent); }
  .contact { position: absolute; top: 1160px; font-family: "Open Sans", sans-serif; font-size: 20px; }
  .contact.web { left: 242px; }
  .contact.mail { left: 502px; }
  .promo-seal { position: absolute; left: 16px; top: 924px; width: 206px; height: 206px; }
</style>
</head>
<body>
<div class="poster">
  <div class="brand-watermark">VITA FORGE</div>

  <svg class="hero-photo" viewBox="0 0 300 1200" role="img" aria-label="Photo of a smiling athlete in black sportswear throwing a punch while driving one knee up">
    <defs>
      <radialGradient id="skin" cx="50%" cy="40%" r="60%">
        <stop offset="0%" stop-color="#b07a58"/>
        <stop offset="55%" stop-color="#5a3a2a"/>
        <stop offset="100%" stop-color="#000000" stop-opacity="0"/>
      </radialGradient>
    </defs>
    <rect x="0" y="0" width="300" height="1200" fill="url(#skin)"/>
  </svg>

  <div class="brand-mark">
    <div class="dot"></div>
    <div class="name">VITA FORGE</div>
    <div class="founder">BY DALE WINTHAM</div>
  </div>

  <div class="rule-top"></div>

  <section class="event-band">
    <div class="venue">Halcott Spires</div>
    <div class="headline">Complimentary</div>
    <div class="subline">Fitness &amp; Wellness Event</div>
  </section>

  <section class="classes-band">
    <div class="line">Complimentary Yoga,</div>
    <div class="line">Pilates &amp; Interval Training</div>
    <div class="line wide">Bootcamp Classes</div>
  </section>

  <div class="offer">
    <span class="plus">+</span>
    <div class="big">Free 30 Minute</div>
    <div class="small">Private Training Sessions</div>
  </div>

  <div class="dates">Sat May 18<sup>th</sup>, 25<sup>th</sup> &amp; June 1<sup>st</sup> Time: 9:00am - 12:15pm</div>

  <section class="schedule">
    <h2>SCHEDULE :</h2>
    <ul>
      <li><b>Yoga</b> 9:00am - 9:30am</li>
      <li><b>Interval Training Bootcamp</b> 9:45am -10:15pm</li>
      <li><b>Pilates</b> 11:45am - 12:15pm</li>
      <li><b>Complimentary Personal Training</b><span class="note">Available 9:00am-12:00pm</span></li>
      <li><b>Kids Karate Classes Also Available</b></li>
    </ul>
  </section>

  <div class="rule-bottom"></div>
  <div class="contact web">www.Vitaforge.tv</div>
  <div class="contact mail">Info@vitaforge.tv</div>

  <svg class="promo-seal" viewBox="0 0 208 208">
    <defs>
      <path id="seal-ring" d="M104,104 m-78,0 a78,78 0 1,1 156,0 a78,78 0 1,1 -156,0"/>
    </defs>
    <circle cx="104" cy="104" r="100" fill="#000" stroke="#fff" stroke-width="4"/>
    <circle cx="104" cy="104" r="58" fill="none" stroke="#fff" stroke-width="3"/>
    <g transform="rotate(-62 104 104)">
      <text font-family="Open Sans, sans-serif" font-weight="700" font-size="24" fill="#fff" letter-spacing="1.5">
        <textPath href="#seal-ring">SPECIAL INTRODUCTORY RATE</textPath>
      </text>
    </g>
    <g transform="rotate(-22 104 104)" font-family="Open Sans, sans-serif" font-weight="700" font-size="11.5" fill="#fff" text-anchor="middle">
      <text x="104" y="84">ON FUTURE</text>
      <text x="104" y="99">PACKAGES</text>
      <text x="104" y="114">DURING</text>
      <text x="104" y="129">PROMOTION</text>
    </g>
  </svg>
</div>
</body>
</html>
```